BRTL web site redesign

Coastal Linkage Engineering service (BRTL) is a diverse technology company specialising in design and installation of fibre optics, network convergence and building services, for commercial clients in Australia, we required a new design of our website to attract new clients, generate sales leads, and provide information about our services to the market. The site and should have a new technology look and feel and be designed in word press. our branding colour is blue.

Target Market(s)

New developments, Construction organisations, Commercial end users, IT managers, Consultants.

Industry/Entity Type

It Company

Number of Pages Required

5+ page

Font styles to use
Sans Serif

Colors
0292cd
3176b5

Requirements
Must have
• key pages.
• Home page with some sizzle, automated pictures running through, I like the look of this competitor website http://www.gleamwirex.com.au/ good clean menus and easy to navigate.
• Services page our key services are Fibre optics, Security, Building services,Electrical. I would like the same page layout (Design) for all our services, with a find out more link on each page, manly picture driven with text around our key messaging.
• About us page with space for company profile and directors pictures, bio and contact information.
• Certifications / Accreditations page with have over 20 certifications on different products from suppliers, and a number of licences from governing bodies.
• Current and past projects page with case studies and customer outcomes
• Contact us page with options around what services they require more information on, please keep in mind the site is around generating sales Leeds and being seen as an industry expert.
Nice to have
• RSS feeds, Linked in link, to be placed within the design, Consistent BRTL branding,Same colour blue as our logo Document library for education information, white papers, presentations etc,
• a new technology look and feel, mobile friendly.
Should not have
• boring layout, move away from our cuurent website http://www.brtlgroup.com.au/
• no e eCommerce store required.

```html
<!DOCTYPE html>
<html lang="en">
<head>
<meta charset="utf-8">
<title>BRTL – Coastal Linkage Engineering Service</title>
<link href="https://fonts.googleapis.com/css2?family=Arimo:wght@400;700&family=Michroma&family=Roboto:wght@400;500&display=swap" rel="stylesheet">
<style>
:root{
  --brand:#0a88c4;
  --brand-bright:#0292cd;
  --brand-deep:#3176b5;
  --ink:#333;
  --muted:#8a8a8a;
  --line:#e6e6e6;
  --footer:#2d2d2d;
  --footer-base:#222;
  --footer-text:#a9a9a9;
}
*{margin:0;padding:0;box-sizing:border-box}
html,body{width:915px;height:1200px;overflow:hidden;background:#fff}
body{position:relative;font-family:"Arimo",Arial,sans-serif;color:var(--ink)}
.abs{position:absolute}

/* header */
.site-header{left:0;top:0;width:915px;height:90px;background:var(--brand)}
.brand{left:75px;top:22px;display:flex;align-items:center;gap:8px}
.brand-mark{width:16px;height:16px;background:#fff}
.brand-name{font-family:"Roboto",sans-serif;font-weight:500;font-size:30px;color:#fff;letter-spacing:1px}
.brand-sub{left:75px;top:59px;font-family:"Roboto",sans-serif;font-size:6.3px;color:#fff;text-transform:uppercase;letter-spacing:.2px}
.main-nav{left:323px;top:36px;display:flex;font-family:"Roboto",sans-serif;font-size:9.5px;color:#fff}
.main-nav a{color:#fff;text-decoration:none;padding:6px 12px;margin-right:6px;border:1px solid transparent;border-radius:2px}
.main-nav a.active{border-color:rgba(255,255,255,.35);background:rgba(255,255,255,.06)}

/* hero */
.hero-band{left:0;top:92px;width:915px;height:382px;background:radial-gradient(ellipse at center,#fff 40%,#ececec 100%);border-bottom:1px solid #e8e8e8}
.slider-frame{left:75px;top:118px;width:764px;height:325px;background:#fff;box-shadow:0 10px 18px -8px rgba(0,0,0,.45)}
.slide{left:80px;top:121px;width:754px;height:316px;background:#000}
.slide-photo{left:80px;top:121px;width:430px;height:316px;background:radial-gradient(ellipse at 35% 30%,#2fb4dc 0%,#0f6f93 30%,#06384d 60%,#000 90%)}
.slide-title{left:531px;top:200px;font-family:"Michroma",sans-serif;font-size:50px;color:var(--brand-bright);letter-spacing:2px}
.slide-sub{left:531px;top:266px;font-family:"Roboto",sans-serif;font-size:14.5px;color:#fff}
.slide-text{left:531px;top:298px;width:290px;font-size:7.4px;line-height:16px;color:#fff}
.dots{left:771px;top:414px;display:flex;gap:4px}
.dots span{width:10px;height:10px;border:1.5px solid #fff;border-radius:50%}
.dots span.on{border-color:var(--brand-bright)}

/* welcome */
.welcome-title{left:0;top:499px;width:915px;text-align:center;font-family:"Michroma",sans-serif;font-size:14px;color:var(--brand);letter-spacing:1px}
.welcome-text{left:120px;top:531px;width:675px;text-align:center;font-size:8px;line-height:17px;color:var(--muted)}
.feature{top:586px;width:240px}
.feature-icon{position:absolute;left:0;top:0;width:38px;height:38px;border-radius:50%;background:var(--brand-deep)}
.feature-icon svg{position:absolute;left:9px;top:9px}
.feature h3{position:absolute;left:52px;top:3px;font-family:"Roboto",sans-serif;font-weight:400;font-size:9.3px;color:#444;white-space:nowrap}
.feature p{position:absolute;left:52px;top:24px;width:200px;font-size:7.4px;line-height:14.5px;color:var(--muted)}
.feature a{position:absolute;left:52px;top:74px;font-family:"Roboto",sans-serif;font-size:7.8px;color:var(--brand);text-decoration:none;white-space:nowrap}
.divider{left:0;top:715px;width:915px;height:1px;background:var(--line)}

/* services */
.services-title{left:75px;top:734px;font-family:"Michroma",sans-serif;font-size:14px;color:var(--brand);letter-spacing:1px}
.services-arrows{left:818px;top:737px;font-size:11px;color:#bbb;letter-spacing:6px}
.card{top:771px;width:182px;height:191px;background:#fff;border:1px solid #e3e3e3;box-shadow:0 1px 2px rgba(0,0,0,.06)}
.card-photo{height:136px}
.card h4{margin:8px 0 0 7px;font-family:"Roboto",sans-serif;font-weight:400;font-size:9.3px;color:#444}
.card p{margin:5px 7px 0;font-size:7.3px;line-height:11.5px;color:var(--muted)}

/* footer */
.site-footer{left:0;top:996px;width:915px;height:161px;background:var(--footer)}
.footer-base{left:0;top:1157px;width:915px;height:43px;background:var(--footer-base)}
.copyright{left:0;top:1174px;width:915px;text-align:center;font-size:7.4px;color:var(--footer-text)}
.fcol h5{font-family:"Roboto",sans-serif;font-weight:400;font-size:10.8px;color:#fff;margin-bottom:11px}
.fcol li{list-style:none;font-size:7.4px;color:var(--footer-text);line-height:15.7px}
.contact-row{display:flex;align-items:center;gap:10px;font-size:7.4px;color:#cfcfcf;line-height:11.5px;margin-bottom:10px}
.contact-ico{width:18px;height:18px;border:1px solid #888;border-radius:50%;display:flex;align-items:center;justify-content:center;flex:none}
.vline{left:653px;top:1014px;width:1px;height:108px;background:#444}
.social{display:flex;gap:5px;margin-bottom:16px}
.social span{width:21px;height:21px;border:1px solid #666}
.news-input{width:149px;height:20px;border:1px solid #777;font-size:6.5px;color:#aaa;padding:6px 7px;margin-bottom:8px}
.news-btn{display:inline-block;border:1px solid #777;font-size:6.5px;color:#ccc;padding:6px 8px}
</style>
</head>
<body>

<header class="abs site-header">
  <div class="abs brand"><span class="brand-mark"></span><span class="brand-name">BRTL</span></div>
  <div class="abs brand-sub">Coastal Linkage Engineering Service</div>
  <nav class="abs main-nav">
    <a class="active" href="#">HOME</a><a href="#">SERVICES</a><a href="#">ABOUT US</a><a href="#">CERTIFICATIONS</a><a href="#">CURRENT / PAST PROJECTS</a><a href="#">CONTACT US</a>
  </nav>
</header>

<section>
  <div class="abs hero-band"></div>
  <div class="abs slider-frame"></div>
  <div class="abs slide"></div>
  <div class="abs slide-photo" role="img" aria-label="Glowing blue fibre optic strands against a dark background"></div>
  <div class="abs slide-title">BRTL</div>
  <div class="abs slide-sub">COASTAL LINKAGE SERVICE</div>
  <p class="abs slide-text">BRTL is diversified technology company 100% Australian owned and operated, we provide Communication, Electrical, Security &amp; ICT services for residential and commercial customers</p>
  <div class="abs dots"><span></span><span class="on"></span><span></span><span></span></div>
</section>

<section>
  <h2 class="abs welcome-title">WELCOME TO BRTL</h2>
  <p class="abs welcome-text">BRTL is diversified technology company 100% Australian owned and operated, we provide Communication, Electrical, Security &amp; ICT services for residential and commercial on innovated solutions that utilises technology advancements which delivers on our customer's expectations.</p>

  <div class="abs feature" style="left:75px">
    <div class="feature-icon"><svg width="20" height="20" viewBox="0 0 20 20" fill="none" stroke="#fff" stroke-width="1.6"><path d="M4 2h8l4 4v12H4z"/><rect x="9" y="11" width="6" height="5" fill="#fff"/><path d="M10.5 11V9.5a1.5 1.5 0 013 0V11"/></svg></div>
    <h3>COMMERCIAL SECURITY SYSTEMS</h3>
    <p>The site includes the protection of heritage buildings, new parklands and community facilities and substan apartments will be built on the site.</p>
    <a href="#">READ MORE &nbsp;›</a>
  </div>
  <div class="abs feature" style="left:338px">
    <div class="feature-icon"><svg width="20" height="20" viewBox="0 0 20 20" fill="none" stroke="#fff" stroke-width="1.6"><ellipse cx="9" cy="4.5" rx="6" ry="2.5"/><path d="M3 4.5v9c0 1.4 2.7 2.5 6 2.5M15 4.5v4M3 9c0 1.4 2.7 2.5 6 2.5"/><circle cx="15" cy="15" r="3.5"/></svg></div>
    <h3>DATA &amp; FIBRE INSTALLATIONS</h3>
    <p>The site includes the protection of heritage buildings, new parklands and community facilities and substan apartments will be built on the site.</p>
    <a href="#">READ MORE &nbsp;›</a>
  </div>
  <div class="abs feature" style="left:604px">
    <div class="feature-icon"><svg width="20" height="20" viewBox="0 0 20 20" fill="none" stroke="#fff" stroke-width="1.6" stroke-linejoin="round"><path d="M12 1L4 11h6l-2 8 8-10h-6z"/></svg></div>
    <h3>ELECTRICAL FIT OUTS</h3>
    <p>The site includes the protection of heritage buildings, new parklands and community facilities and substan apartments will be built on the site.</p>
    <a href="#">READ MORE &nbsp;›</a>
  </div>
  <div class="abs divider"></div>
</section>

<section>
  <h2 class="abs services-title">OUR SERVICES</h2>
  <div class="abs services-arrows">‹ ›</div>
  <article class="abs card" style="left:75px">
    <div class="card-photo" role="img" aria-label="Technician with a laptop beside a fibre optic server rack" style="background:linear-gradient(90deg,#8c99a6,#d9dde2 55%,#f3f3f3)"></div>
    <h4>FIBRE OPTICS</h4>
    <p>BRTL is diversified technology company 100% residential and commercial customers.....</p>
  </article>
  <article class="abs card" style="left:270px">
    <div class="card-photo" role="img" aria-label="Smartphone showing a padlock over a security word cloud" style="background:linear-gradient(135deg,#c9c9c9,#e8e8e8 50%,#b7b7b7)"></div>
    <h4>SECURITY</h4>
    <p>BRTL is diversified technology company 100% residential and commercial customers.....</p>
  </article>
  <article class="abs card" style="left:464px">
    <div class="card-photo" role="img" aria-label="Worker in hard hat installing solar panels" style="background:linear-gradient(135deg,#6f8fb4,#aec4dc 50%,#32507a)"></div>
    <h4>BUILDING SERVICES</h4>
    <p>BRTL is diversified technology company 100% residential and commercial customers.....</p>
  </article>
  <article class="abs card" style="left:658px">
    <div class="card-photo" role="img" aria-label="Hands operating a fibre splicing machine with cables" style="background:linear-gradient(135deg,#3a4450,#6c7a86 50%,#1f2a33)"></div>
    <h4>ELECTRICAL</h4>
    <p>BRTL is diversified technology company 100% residential and commercial customers.....</p>
  </article>
</section>

<footer>
  <div class="abs site-footer"></div>
  <div class="abs fcol" style="left:77px;top:1014px"><h5>MY ACCOUNT</h5><ul><li>My Account</li><li>Sign In</li><li>Order Status</li><li>My Cart</li><li>My Wishlist</li></ul></div>
  <div class="abs fcol" style="left:196px;top:1014px"><h5>INFORMATION</h5><ul><li>INFORMATION</li><li>About Us</li><li>Services</li><li>ISP</li><li>Recent Projects</li><li>Contact Us</li><li>Blog</li></ul></div>
  <div class="abs fcol" style="left:325px;top:1014px"><h5>SERVICES</h5><ul><li>Commercial Security Systems</li><li>Data &amp; Fibre Installations</li><li>Information Communication &amp; Technology</li><li>Electrical fit outs</li></ul></div>
  <div class="abs fcol" style="left:496px;top:1014px"><h5>CONTACT US</h5>
    <div class="contact-row"><span class="contact-ico"><svg width="8" height="10" viewBox="0 0 8 10" fill="none" stroke="#ccc"><path d="M4 9.5S7 6 7 4A3 3 0 001 4c0 2 3 5.5 3 5.5z"/><circle cx="4" cy="4" r="1"/></svg></span><span>Suite 4B, 12-14 Marlow Parade<br>Harbourvale NSW 2199</span></div>
    <div class="contact-row"><span class="contact-ico"><svg width="6" height="9" viewBox="0 0 6 9" fill="none" stroke="#ccc"><rect x="0.5" y="0.5" width="5" height="8" rx="1"/></svg></span><span>1300 555 019</span></div>
    <div class="contact-row"><span class="contact-ico"><svg width="9" height="7" viewBox="0 0 9 7" fill="none" stroke="#ccc"><rect x="0.5" y="0.5" width="8" height="6"/><path d="M.5.5l4 3.5 4-3.5"/></svg></span><span>info@brtlgroup.com</span></div>
  </div>
  <div class="abs vline"></div>
  <div class="abs fcol" style="left:677px;top:1014px"><h5>CONNECT WITH US</h5>
    <div class="social"><span></span><span></span><span></span><span></span></div>
    <h5>GET NEWSLETTER</h5>
    <div class="news-input">EMAIL ADDRESS :</div>
    <span class="news-btn">SUBSCRIBE</span>
  </div>
  <div class="abs footer-base"></div>
  <div class="abs copyright">© Copy Rights 2014BRTL GROUP.All Rights Reserved.</div>
</footer>

</body>
</html>
```